Business Book - Building Calm Mornings at the Office (Hand Off the Small Stuff and Keep the Spark)

I'm looking for a cover that appeals to successful business people who are used to reading business titles.

The cover should feel familiar and fit in with the existing canon of bestselling business books with a vibrant, but professional look (see attached).

I want my book to stand out, but not to be frivolous. Abstract is probably best. Or close to it.

Please feel free to use my brand colours, or go with something else -

Teal
HEX #199BAB
25 / 155 / 171

Coral
HEX #EE786E
238 / 120/ 110

I don't want to include anything connected with robots or gendered assistants/business people. Or headsets.

It's only 24 hours which is mental

```html
<!DOCTYPE html>
<html lang="en">
<head>
<meta charset="utf-8">
<title>Building Calm Mornings at the Office – Cover Wrap</title>
<link href="https://fonts.googleapis.com/css2?family=Bebas+Neue&family=Great+Vibes&family=Lato:wght@400&family=Montserrat:wght@400;600&family=Open+Sans:wght@400;600&display=swap" rel="stylesheet">
<style>
  :root {
    --backdrop: #7f413c;
    --paper: #ffffff;
    --title: #a3514d;
    --coral: #ee786e;
    --blush: #fbb7ad;
    --blush-soft: #fde3de;
    --ink: #141414;
    --body: #1e1e1e;
    --muted: #555555;
  }
  * { box-sizing: border-box; margin: 0; padding: 0; }
  html, body { width: 1200px; height: 960px; overflow: hidden; background: var(--backdrop); }
  .canvas { position: relative; width: 1200px; height: 960px; background: var(--backdrop); overflow: hidden; }

  .wrap { position: absolute; left: 80px; top: 119px; width: 1040px; height: 720px; background: var(--paper); }
  .wrap-texture {
    position: absolute; inset: 0;
    background: linear-gradient(180deg, var(--paper) 0%, var(--paper) 32%, var(--blush-soft) 52%, #fccbc3 72%, var(--blush) 100%);
  }

  .abs { position: absolute; }
  .bebas { font-family: "Bebas Neue", "Oswald", sans-serif; color: var(--title); line-height: 1; white-space: nowrap; font-weight: 400; }

  /* Back cover */
  .back-kicker { left: 120px; width: 412px; top: 261px; text-align: center; font-size: 25px; }
  .back-title { left: 120px; width: 412px; top: 284px; text-align: center; font-size: 34px; }
  .rule { height: 1.5px; background: var(--coral); }
  .back-rule { left: 288px; top: 324px; width: 67px; }
  .blurb { left: 119px; top: 336px; width: 420px; font-family: "Lato", sans-serif; font-size: 10.4px; line-height: 16.7px; color: var(--body); }
  .blurb p { margin-bottom: 8.7px; }
  .author-photo {
    float: left; width: 85px; height: 88px; margin: 5px 9px 0 2px; background: var(--paper);
    display: flex; align-items: center; justify-content: center; text-align: left;
    font-family: "Open Sans", sans-serif; font-weight: 400; font-size: 10px; line-height: 1.2; color: var(--muted);
  }
  .isbn-box {
    left: 361px; top: 719px; width: 174px; height: 87px; background: var(--paper);
    display: flex; align-items: center; justify-content: center;
    font-family: "Lato", sans-serif; font-size: 18px; color: var(--muted);
  }

  /* Spine */
  .spine-text { writing-mode: vertical-rl; }
  .spine-kicker { left: 602px; top: 293px; font-size: 23px; }
  .spine-title { left: 574px; top: 266px; font-size: 31px; }
  .spine-author { left: 586px; top: 490px; font-family: "Montserrat", sans-serif; font-weight: 600; font-size: 26px; letter-spacing: .5px; color: var(--ink); white-space: nowrap; }

  /* Front cover */
  .front-line-1 { left: 751px; width: 261px; top: 260px; text-align: center; font-size: 68px; }
  .front-line-2 { left: 751px; width: 261px; top: 305px; text-align: center; font-size: 150px; letter-spacing: 1px; }
  .front-line-3 { left: 846px; top: 436px; font-size: 40px; }
  .front-script { left: 752px; top: 476px; font-family: "Great Vibes", cursive; font-size: 84px; line-height: 1; color: var(--title); white-space: nowrap; }
  .front-line-4 { left: 782px; width: 223px; top: 536px; text-align: center; font-size: 66px; }
  .front-rule { left: 848px; top: 611px; width: 66px; }
  .subtitle { left: 720px; width: 322px; top: 625px; text-align: center; font-family: "Montserrat", sans-serif; font-size: 17px; line-height: 28px; letter-spacing: .8px; color: var(--ink); }
  .front-author { left: 740px; width: 282px; top: 738px; text-align: center; font-family: "Open Sans", sans-serif; font-weight: 600; font-size: 38px; line-height: 1; color: var(--ink); white-space: nowrap; }
</style>
</head>
<body>
<div class="canvas">
  <div class="wrap">
    <div class="wrap-texture" role="img" aria-label="Soft coral rippling water texture fading to white at the top"></div>
  </div>

  <!-- Back cover -->
  <div class="abs bebas back-kicker">Building Calm Mornings</div>
  <div class="abs bebas back-title">At the Office</div>
  <div class="abs rule back-rule"></div>
  <div class="abs blurb">
    <p>Lorem Ipsum is simply dummy text of the printing and typesetting industry. Lorem Ipsum has been the industry's standard dummy text ever since the 1500s, when an Lorem Ipsum passags, and more recently with desktop pubng software like Marlow PageSet includi versions of Lorem Ipsum.</p>
    <p>Lorem Ipsum is simply dummy text of the printing and typesetting industry. Lorem Ipsum has been the industry's standard dummy text ever since the 1500s, when an Lorem Ipsum passags, and more recently with desktop pubng software like Marlow PageSet includi versions of Lorem Ipsum. Lorem Ipsum is simply dummy text of the printing and typesetting industry. when an Lorem Ipsum passags, and more recently with desktop pubng software like Marlow PageSet includi versions of Lorem Ipsum. Lorem Ipsum is simply dummy text of the printing and typesetting industry. Lorem Ipsum has been the software like Marlow PageSet includi versions of Lorem Ipsum.</p>
    <div class="author-photo" role="img" aria-label="Author portrait placeholder">author<br>image</div>
    <p>Lorem Ipsum is simply dummy text of the printing and typesetting industry. Lorem Ipsum has been the industry's standard dummy text ever since the 1500s, when an Lorem Ipsum passags, and more recently with desktop pubng software like Marlow PageSet includi versions of Lorem Ipsum. Lorem Ipsum is simply dummy text of the printing and typesetting industry. Lorem Ipsum has been the industry's standard dummy text ever since the 1500s, when an Lorem Ipsum passags, and more recently with desktop pubng software like Marlow PageSet includi versions of Lorem Ipsum. Lorem Ipsum is simply dummy text of the printing and typesetting industry.</p>
  </div>
  <div class="abs isbn-box">ISBN</div>

  <!-- Spine -->
  <div class="abs bebas spine-text spine-kicker">Building Calm Mornings</div>
  <div class="abs bebas spine-text spine-title">At the Office</div>
  <div class="abs spine-text spine-author">AUTHOR NAME</div>

  <!-- Front cover -->
  <h1 class="abs bebas front-line-1">Building</h1>
  <div class="abs bebas front-line-2">Calm</div>
  <div class="abs bebas front-line-3">Mornings</div>
  <div class="abs front-script">at the</div>
  <div class="abs bebas front-line-4">Office</div>
  <div class="abs rule front-rule"></div>
  <p class="abs subtitle">Hand Off the Small Stuff<br>and Keep the Spark</p>
  <div class="abs front-author">AUTHOR NAME</div>
</div>
</body>
</html>
```